Commercial/Corporate Law Firm needs Website Design

Hi guys. I've started up a new law firm and would love your help designing an attractive website. I'll need both design and coding, and to make it easy for us to edit as necessary later, I think it should be built off a Wordpress.org structure.
FIRST IMPRESSIONS
It's very important that the first impression of the website really captures our prospective clients' attention and impresses them. Their first three seconds needs to be good.
I imagine the homepage may be short, with a menu bar and a compelling image, and with a tagline overlaid or underneath (eg. "It's about results.")
The image should be related to our practice areas: eg. IPOs, corporate transactions, or commercial negotiations.
I have previously suggested there could be a skyline image of Sydney or Adelaide. However, because we are based in Adelaide, I don't think Sydney is appropriate - and Adelaide is probably too boring to use.
HOMEPAGE
Being a new firm, we don't have many existing testimonials, and I will be the only lawyer to start with. So we need to focus on the nature of the services we will provide and how my experience can help them. We have an existing logo to use, and I would like the website colour scheme not to clash with that logo (dark blue and white).
After the initial image and tagline there should be a brief introduction to each of the main areas of work, eg. "We specialise in three main areas of practice:"
1. Corporate Transactions and Regulation
2. Business Law and Dispute Resolution
3. Migration Assistance
These should each have an appropriate photo and link to a separate page that briefly describes our services in that area.
Below that there should be a message from me with a photo. Finally, at the bottom, there should be a "Contact Us" section which shows a Google image of our address, contact details, and then our logo with colours inverted.
OTHER PAGES
While we will need some other pages, they should all be fairly simple. I think we will need one page to say "About Us", where I will put information about my experience. I think we will then need one page for each of the 3 areas listed above, which just needs an appropriate image and then text to describe the service. Finally, a "Contact Us" page which I imagine will be the same as the bottom of the homepage.
OTHER DETAILS
For now you can use details from my LinkedIn page to fill out any other text as necessary, or the photo.
Because the logo is square, I would prefer the design of the website also to be rectangular.
Looking forward to seeing your work! Thank you.
Marcus
Potential clients:
Businesses with legal issues or disputes
Companies wishing to list on the stock market

```html
<!DOCTYPE html>
<html lang="en">
<head>
<meta charset="utf-8">
<title>Harrow Legal</title>
<link rel="stylesheet" href="https://fonts.googleapis.com/css2?family=Montserrat:wght@400;500;600;700;800&family=Mulish:wght@400;600;700&display=swap">
<style>
:root{
  --navy:#1a3461;
  --navy-deep:#173059;
  --blue:#1565d8;
  --blue-band:#1470d0;
  --ink:#1b2b4a;
  --text:#222;
  --muted:#666;
  --white:#fff;
  --line:#dfe5ee;
}
*{box-sizing:border-box;margin:0;padding:0}
html,body{width:1200px;height:2293px;overflow:hidden;background:var(--white)}
body{position:relative;font-family:"Mulish",Arial,sans-serif;color:var(--text)}
.abs{position:absolute}

/* header */
.site-header{left:0;top:0;width:1200px;height:156px;background:var(--white)}
.brand{left:78px;top:48px;display:flex;align-items:center;gap:14px}
.brand-square{width:48px;height:48px;background:var(--navy)}
.brand-name{font-family:"Montserrat",sans-serif;font-weight:600;font-size:26px;color:var(--navy);letter-spacing:2px}
.contact-item{top:46px;display:flex;gap:16px;align-items:center}
.contact-icon{width:52px;height:58px;border:2px solid var(--blue);display:flex;align-items:center;justify-content:center}
.contact-label{font-family:"Montserrat",sans-serif;font-size:18px;color:var(--blue);margin-bottom:6px}
.contact-value{font-family:"Montserrat",sans-serif;font-size:20px;font-weight:500;color:var(--ink)}

/* nav */
.main-nav{left:0;top:156px;width:1200px;height:62px;background:var(--navy)}
.nav-link{top:0;line-height:62px;font-family:"Montserrat",sans-serif;font-size:15px;color:var(--white);text-transform:uppercase}
.nav-cta{left:760px;top:6px;width:208px;height:51px;background:var(--blue);color:var(--white);font-family:"Montserrat",sans-serif;font-size:15px;text-align:center;line-height:51px;text-transform:uppercase}
.nav-search{left:1002px;top:17px}

/* hero */
.hero{left:0;top:218px;width:1200px;height:574px;background:linear-gradient(90deg,#6f7890 0%,#c9ced8 40%,#e6ebf1 65%,#f1f4f7 100%)}
.hero-title{left:722px;top:388px;font-family:"Montserrat",sans-serif;font-weight:800;font-size:36px;color:var(--blue);text-shadow:2px 3px 4px rgba(0,0,0,.35)}
.hero-text{left:722px;top:448px;width:405px;font-size:16px;line-height:25px;font-weight:600;color:#111}
.hero-btn{left:722px;top:546px;width:168px;height:62px;background:var(--navy);color:var(--white);font-family:"Montserrat",sans-serif;font-size:18px;text-align:center;line-height:62px;box-shadow:0 3px 6px rgba(0,0,0,.3)}
.hero-dots{left:548px;top:755px;width:104px;height:37px;background:var(--blue);clip-path:polygon(8% 0,92% 0,100% 100%,0 100%);display:flex;gap:7px;justify-content:center;align-items:center}
.dot{width:13px;height:13px;border-radius:50%;border:2px solid var(--white)}
.dot.active{background:var(--white)}

/* why choose us */
.section-title{left:0;width:1200px;text-align:center;font-family:"Montserrat",sans-serif;font-weight:700;color:var(--navy)}
.why-title{top:850px;font-size:37px}
.service-card{left:78px;width:469px;height:166px;background:var(--white);border-radius:6px;box-shadow:0 4px 18px rgba(0,0,0,.1)}
.service-icon{position:absolute;left:18px;top:24px}
.service-name{position:absolute;left:137px;top:24px;width:268px;font-family:"Montserrat",sans-serif;font-weight:700;font-size:19px;line-height:26px;color:var(--ink)}
.service-text{position:absolute;left:137px;width:290px;font-size:13.5px;line-height:25px;color:var(--muted)}
.principal-photo{left:582px;top:948px;width:543px;height:626px;background:linear-gradient(180deg,#d9d6d4 0%,#4a4d5e 40%,#23273a 100%)}

/* contact band */
.contact-band{left:0;top:1574px;width:1200px;height:459px;background:var(--blue-band)}
.band-title{top:1632px;font-size:34px;color:var(--white);font-weight:600}
.field{background:var(--white);border-radius:3px;box-shadow:0 2px 3px rgba(0,0,0,.25);font-size:13px;color:#555;padding:0 12px;line-height:62px}
.field.area{line-height:20px;padding-top:20px}
.send-btn{left:612px;top:1886px;width:230px;height:63px;background:var(--navy);color:var(--white);font-family:"Montserrat",sans-serif;font-size:18px;text-align:center;line-height:63px;border-radius:2px}

/* footer */
.site-footer{left:0;top:2033px;width:1200px;height:192px;background:linear-gradient(180deg,#4a5770 0%,#2c3a55 60%,#1e2c47 100%)}
.footer-pin{left:78px;top:2087px;width:40px;height:40px;border-radius:50%;background:var(--white);display:flex;align-items:center;justify-content:center}
.footer-brand{left:136px;top:2084px;font-family:"Montserrat",sans-serif;font-weight:700;font-size:19px;color:var(--white)}
.footer-about{left:136px;top:2113px;width:230px;font-size:14px;line-height:25px;color:#e6e9ef}
.footer-links{left:418px;top:2087px;display:flex;gap:16px;font-size:14px;color:var(--white)}
.footer-links .sep{opacity:.7}
.social{top:2138px;width:30px;height:30px;border-radius:50%;background:var(--blue);border:2px solid var(--white)}
.footer-contact{left:890px;display:flex;align-items:center;gap:18px;font-size:15px;color:var(--white)}
.footer-contact .round{width:41px;height:41px;border-radius:50%;background:var(--white);display:flex;align-items:center;justify-content:center}
.copyright{left:0;top:2225px;width:1200px;height:68px;background:var(--navy-deep);text-align:center;line-height:68px;font-size:14px;color:#e7ebf2}
.copyright strong{font-weight:700;color:var(--white)}
</style>
</head>
<body>

<header class="site-header abs">
  <div class="brand abs"><span class="brand-square"></span><span class="brand-name">HARROW LEGAL</span></div>
  <div class="contact-item abs" style="left:570px">
    <div class="contact-icon"><svg width="24" height="24" viewBox="0 0 24 24"><path fill="#1565d8" d="M6.6 10.8a15.1 15.1 0 0 0 6.6 6.6l2.2-2.2a1 1 0 0 1 1-.25c1.1.37 2.3.57 3.6.57a1 1 0 0 1 1 1V20a1 1 0 0 1-1 1A17 17 0 0 1 3 4a1 1 0 0 1 1-1h3.5a1 1 0 0 1 1 1c0 1.25.2 2.45.57 3.57a1 1 0 0 1-.25 1z"/></svg></div>
    <div><div class="contact-label">Call Us</div><div class="contact-value">1800-555-0142</div></div>
  </div>
  <div class="contact-item abs" style="left:830px">
    <div class="contact-icon"><svg width="28" height="20" viewBox="0 0 28 20"><rect x="1" y="1" width="26" height="18" fill="#1565d8"/><path d="M1 1l13 10L27 1" fill="none" stroke="#fff" stroke-width="2"/></svg></div>
    <div><div class="contact-label">Email Us</div><div class="contact-value">info@harrowlegal.com</div></div>
  </div>
</header>

<nav class="main-nav abs">
  <span class="nav-link abs" style="left:175px">Home</span>
  <span class="nav-link abs" style="left:289px">About</span>
  <span class="nav-link abs" style="left:410px">Practice Areas</span>
  <span class="nav-link abs" style="left:614px">Contact</span>
  <span class="nav-cta abs">Free Consultation</span>
  <svg class="nav-search abs" width="26" height="26" viewBox="0 0 26 26"><circle cx="10" cy="10" r="8" fill="none" stroke="#fff" stroke-width="2"/><path d="M16 16l8 8" stroke="#fff" stroke-width="2"/></svg>
</nav>

<div class="hero abs" role="img" aria-label="Photo of two smiling business professionals in suits in a bright office"></div>
<h1 class="hero-title abs">WE GET RESULTS</h1>
<p class="hero-text abs">Lorem ipsum dolor sit amet, consectetur adipiscing elit, sed do eiusmod tempor incididunt ut labore et dolore magna aliqua.</p>
<span class="hero-btn abs">CONTACT US</span>
<div class="hero-dots abs"><span class="dot"></span><span class="dot active"></span><span class="dot"></span></div>

<h2 class="section-title why-title abs">Why Choose Us</h2>

<article class="service-card abs" style="top:949px">
  <svg class="service-icon" width="84" height="56" viewBox="0 0 84 56"><g fill="#1565d8"><circle cx="20" cy="10" r="6"/><circle cx="42" cy="8" r="6"/><circle cx="64" cy="10" r="6"/><rect x="24" y="22" width="36" height="16"/><rect x="4" y="20" width="12" height="20"/><rect x="68" y="20" width="12" height="20"/><rect x="2" y="42" width="80" height="4"/><rect x="8" y="46" width="4" height="10"/><rect x="72" y="46" width="4" height="10"/></g></svg>
  <h3 class="service-name">Business Law and Dispute Resolution</h3>
  <p class="service-text" style="top:86px">Lorem Ipsum is simply dummy text of the printing and typesetting industry.</p>
</article>

<article class="service-card abs" style="top:1136px">
  <svg class="service-icon" width="84" height="70" viewBox="0 0 84 70" style="top:22px"><g fill="none" stroke="#1565d8" stroke-width="4"><circle cx="42" cy="35" r="14"/><path d="M26 10v50M62 10v50"/></g><path d="M26 60l-8-10h16zM62 8l-8 10h16z" fill="#1565d8"/><text x="42" y="41" font-family="Montserrat,sans-serif" font-size="16" font-weight="700" fill="#1565d8" text-anchor="middle">$</text></svg>
  <h3 class="service-name">Corporate Transactions and Regulation</h3>
  <p class="service-text" style="top:86px">Lorem Ipsum is simply dummy text of the printing and typesetting industry.</p>
</article>

<article class="service-card abs" style="top:1324px">
  <svg class="service-icon" width="84" height="64" viewBox="0 0 84 64"><g fill="none" stroke="#1565d8" stroke-width="4"><path d="M40 6h28v52H40"/><path d="M10 32h40M6 22h20M6 42h20"/></g><path d="M56 32l-10-9v18z" fill="#1565d8"/></svg>
  <h3 class="service-name">Migration Assistance</h3>
  <p class="service-text" style="top:60px">Lorem Ipsum is simply dummy text of the printing and typesetting industry. Lorem dummy text ever since the 1500s,</p>
</article>

<div class="principal-photo abs" role="img" aria-label="Portrait photo of a smiling lawyer in a dark suit and red tie"></div>

<section class="contact-band abs"></section>
<h2 class="section-title band-title abs">If you need, Just drop us a line</h2>
<div class="field abs" style="left:143px;top:1720px;width:448px;height:62px">Enter Your Name :</div>
<div class="field abs" style="left:143px;top:1803px;width:448px;height:63px">Enter Your Email :</div>
<div class="field abs" style="left:143px;top:1886px;width:448px;height:63px">Your Subject :</div>
<div class="field area abs" style="left:612px;top:1720px;width:447px;height:146px">Message / Comments :</div>
<span class="send-btn abs">SEND MESSAGE</span>

<footer class="site-footer abs" role="img" aria-label="Dark blue city skyline photo behind the footer"></footer>
<div class="footer-pin abs"><svg width="16" height="22" viewBox="0 0 16 22"><path d="M8 0a8 8 0 0 1 8 8c0 6-8 14-8 14S0 14 0 8a8 8 0 0 1 8-8z" fill="#1565d8"/><circle cx="8" cy="8" r="3" fill="#fff"/></svg></div>
<div class="footer-brand abs">HARROW LEGAL</div>
<p class="footer-about abs">Lorem Ipsum is simply dummy printing and typesetting industry.</p>
<div class="footer-links abs"><span>Home</span><span class="sep">|</span><span>About Us</span><span class="sep">|</span><span>Practice Area</span><span class="sep">|</span><span>Contact Us</span></div>
<span class="social abs" style="left:549px" aria-label="Social link"></span>
<span class="social abs" style="left:584px" aria-label="Social link"></span>
<span class="social abs" style="left:619px" aria-label="Social link"></span>
<div class="footer-contact abs" style="top:2081px"><span class="round"><svg width="18" height="18" viewBox="0 0 24 24"><path fill="#1a3461" d="M6.6 10.8a15.1 15.1 0 0 0 6.6 6.6l2.2-2.2a1 1 0 0 1 1-.25c1.1.37 2.3.57 3.6.57a1 1 0 0 1 1 1V20a1 1 0 0 1-1 1A17 17 0 0 1 3 4a1 1 0 0 1 1-1h3.5a1 1 0 0 1 1 1c0 1.25.2 2.45.57 3.57a1 1 0 0 1-.25 1z"/></svg></span>1800-555-0142</div>
<div class="footer-contact abs" style="top:2137px"><span class="round"><svg width="18" height="13" viewBox="0 0 28 20"><rect x="1" y="1" width="26" height="18" fill="#1a3461"/><path d="M1 1l13 10L27 1" fill="none" stroke="#fff" stroke-width="2"/></svg></span>info@harrowlegal.com</div>
<div class="copyright abs">© Copyright 2018, <strong>HARROW LEGAL</strong> . All rights reserved.</div>

</body>
</html>
```